Business Card - connecting 2 souls and beggining the journey of self discovery

Logo on the front
with tag line

On the back list of services and contact details

Seminars
workshops
Coaching
podcasts

Darren Whitlow
Health & Wellbeing Life Coach
0491 372 615
darren@brightcoreliving.example
brightcoreliving.example

Industry/Entity Type

Life Coaching

Contact Information for Business Card

I like the use of colour from the logo to be used. I'm not a fan of white.

Requirements
Must have
• My tagline: The journey home starts with you
Nice to have
• Use of colour that is in the Brightcore logo

```html
<!DOCTYPE html>
<html lang="en">
<head>
<meta charset="utf-8">
<title>Brightcore – Business Card</title>
<link href="https://fonts.googleapis.com/css2?family=Montserrat:wght@300;400;600;700&family=Roboto:wght@400;500;700&display=swap" rel="stylesheet">
<style>
  :root{
    --backdrop:#2b2c2e;
    --card-grey:#7d7e80;
    --card-white:#f7f7f6;
    --ink-grey:#6f7072;
    --green-core:#8cc63f;
    --green-edge:#4caa8a;
    --purple:#8e44c9;
    --magenta:#d3479a;
    --coral:#f0605a;
    --amber:#f6b52a;
    --leaf:#7cc34a;
    --teal:#3fb39a;
    --white:#ffffff;
  }
  *{margin:0;padding:0;box-sizing:border-box}
  html,body{width:1200px;height:886px;overflow:hidden;background:var(--backdrop)}
  .canvas{position:relative;width:1200px;height:886px}

  .card{position:absolute;left:305px;width:590px;height:340px;border-radius:18px;overflow:hidden}

  /* Services side */
  .card--services{top:60px;
    background:radial-gradient(ellipse at 48% 42%, var(--green-core) 0%, #6cba5a 45%, var(--green-edge) 100%);}
  .brand-mark{position:absolute;left:50%;top:44%;transform:translate(-50%,-50%);
    display:flex;align-items:center;gap:14px}
  .brand-mark__dot{width:34px;height:34px;border-radius:50%;background:var(--white)}
  .brand-mark__name{font-family:"Montserrat",sans-serif;font-weight:600;font-size:34px;color:var(--white);letter-spacing:.5px}
  .services{position:absolute;right:34px;bottom:30px;text-align:right;
    font-family:"Roboto",sans-serif;font-size:13px;line-height:1.45;color:var(--white)}

  /* Contact side */
  .card--contact{top:486px;background:var(--card-grey)}
  .card__art{position:absolute;inset:0}
  .identity{position:absolute;left:34px;top:64px;width:310px}
  .identity__mark{display:flex;align-items:center;gap:10px;margin-bottom:26px}
  .identity__dot{width:22px;height:22px;border-radius:50%;background:var(--purple)}
  .identity__name{font-family:"Montserrat",sans-serif;font-weight:600;font-size:20px;color:var(--purple)}
  .identity__headline{font-family:"Montserrat",sans-serif;font-weight:300;font-size:27px;color:var(--ink-grey);letter-spacing:-.3px}
  .identity__tagline{font-family:"Montserrat",sans-serif;font-weight:400;font-size:14.5px;color:var(--ink-grey);margin-top:4px}

  .contact{position:absolute;left:372px;top:112px;width:210px;color:var(--white);font-family:"Roboto",sans-serif}
  .contact__name{font-weight:700;font-size:21px;text-transform:uppercase;letter-spacing:.2px}
  .contact__role{font-weight:400;font-size:10.5px;text-transform:uppercase;margin-top:3px;margin-bottom:20px}
  .contact__line{display:flex;align-items:center;gap:7px;font-size:12px;margin-top:6px;white-space:nowrap}
  .contact__line svg{width:11px;height:11px;flex:none;fill:var(--white)}
</style>
</head>
<body>
<main class="canvas">

  <section class="card card--services">
    <div class="brand-mark">
      <span class="brand-mark__dot"></span>
      <span class="brand-mark__name">Brightcore</span>
    </div>
    <p class="services">Seminars • Workshops<br>Coaching • Podcasts</p>
  </section>

  <section class="card card--contact">
    <svg class="card__art" viewBox="0 0 590 340" width="590" height="340" aria-hidden="true">
      <defs>
        <linearGradient id="spectrum" x1="0" y1="1" x2="0.3" y2="0">
          <stop offset="0" stop-color="#8e44c9"/>
          <stop offset="0.25" stop-color="#d3479a"/>
          <stop offset="0.45" stop-color="#f0605a"/>
          <stop offset="0.65" stop-color="#f6b52a"/>
          <stop offset="0.85" stop-color="#7cc34a"/>
          <stop offset="1" stop-color="#3fb39a"/>
        </linearGradient>
      </defs>
      <circle cx="90" cy="150" r="268" fill="none" stroke="url(#spectrum)" stroke-width="7"
              stroke-dasharray="150 4 110 4 120 4 2000"/>
      <circle cx="90" cy="150" r="262" fill="var(--card-white)"/>
    </svg>

    <div class="identity">
      <div class="identity__mark">
        <span class="identity__dot"></span>
        <span class="identity__name">Brightcore</span>
      </div>
      <h1 class="identity__headline">Home of Bright Living</h1>
      <p class="identity__tagline">The journey home starts with you</p>
    </div>

    <div class="contact">
      <h2 class="contact__name">Darren Whitlow</h2>
      <p class="contact__role">Health &amp; Wellbeing Life Coach</p>
      <p class="contact__line">
        <svg viewBox="0 0 24 24"><path d="M6.6 10.8a15.1 15.1 0 0 0 6.6 6.6l2.2-2.2a1 1 0 0 1 1-.25 11.4 11.4 0 0 0 3.6.57 1 1 0 0 1 1 1V20a1 1 0 0 1-1 1A17 17 0 0 1 3 4a1 1 0 0 1 1-1h3.5a1 1 0 0 1 1 1c0 1.25.2 2.45.57 3.57a1 1 0 0 1-.25 1z"/></svg>
        0491 372 615
      </p>
      <p class="contact__line">
        <svg viewBox="0 0 24 24"><path d="M2 5h20v14H2z M2 5l10 8 10-8" fill="none" stroke="#fff" stroke-width="2.4"/></svg>
        darren@brightcoreliving.example
      </p>
      <p class="contact__line">
        <svg viewBox="0 0 24 24"><circle cx="12" cy="12" r="9.5" fill="none" stroke="#fff" stroke-width="2.4"/><path d="M2.5 12h19M12 2.5c3 3 3 16 0 19M12 2.5c-3 3-3 16 0 19" fill="none" stroke="#fff" stroke-width="1.8"/></svg>
        brightcoreliving.example
      </p>
    </div>
  </section>

</main>
</body>
</html>
```